Business Card Design for Training Business

Clear Path Coaching is a new business that delivers training and other services with a focus on topics related to mental health and wellbeing, for example, Wellmind Response Course, Resilience etc. We have a strong focus on evidence-based psychology and neuroscience. I have a logo which I will upload with the brief, so please consider colours that work well with the logo.
Target Market(s)
Adults, workplaces (particularly government and not-for-profits)
Industry/Entity Type
Business
Contact Information for Business Card
Head Strong TrainingSamantha SellwoodDirector0438 770 850sam@headstrongtraining.com.auwww.headstrongtraining.com.au

```html
<!DOCTYPE html>
<html lang="en">
<head>
<meta charset="utf-8">
<title>Clear Path Coaching – Business Card</title>
<link rel="stylesheet" href="https://fonts.googleapis.com/css2?family=Lato:wght@300;400;700&display=swap">
<style>
  :root {
    --backdrop: #2f2d2c;
    --band-dark: #050505;
    --band-teal: #2ccfd3;
    --brand-grey: #9ea6a6;
    --ink: #1b1b1b;
    --rule: #222222;
  }
  html, body {
    margin: 0;
    padding: 0;
    width: 1200px;
    height: 1200px;
    overflow: hidden;
    background: var(--backdrop);
  }
  .canvas {
    position: relative;
    width: 1200px;
    height: 1200px;
    display: flex;
    align-items: center;
    justify-content: center;
  }
  .business-card {
    position: relative;
    width: 1000px;
    height: 611px;
    background: var(--band-teal);
    font-family: "Lato", sans-serif;
    color: var(--ink);
    box-shadow: 0 18px 40px rgba(0,0,0,0.35);
  }
  .brand-band {
    position: absolute;
    top: 0; left: 0; right: 0;
    height: 290px;
    background: var(--band-dark);
    display: flex;
    flex-direction: column;
    align-items: center;
  }
  .brand-mark {
    margin-top: 58px;
    width: 104px;
    height: 104px;
    border-radius: 50%;
    border: 3px solid var(--brand-grey);
    box-sizing: border-box;
  }
  .brand-name {
    margin-top: 30px;
    font-weight: 300;
    font-size: 36px;
    letter-spacing: 5px;
    text-transform: uppercase;
    color: var(--brand-grey);
  }
  .contact-area {
    position: absolute;
    top: 340px; left: 0; right: 0;
    height: 210px;
  }
  .person {
    position: absolute;
    right: 520px;
    top: 14px;
    text-align: right;
  }
  .person-name {
    font-weight: 300;
    font-size: 34px;
    margin: 0 0 8px;
  }
  .person-role {
    font-weight: 700;
    font-size: 24px;
    margin: 0 0 4px;
  }
  .person-company {
    font-weight: 400;
    font-size: 24px;
    margin: 0;
  }
  .divider {
    position: absolute;
    left: 505px;
    top: 0;
    width: 2px;
    height: 210px;
    background: var(--rule);
  }
  .contact-list {
    position: absolute;
    left: 535px;
    top: 48px;
    margin: 0;
    padding: 0;
    list-style: none;
  }
  .contact-item {
    display: flex;
    align-items: center;
    gap: 14px;
    font-weight: 400;
    font-size: 23px;
    height: 38px;
  }
  .contact-icon {
    width: 22px;
    height: 22px;
    flex: none;
  }
</style>
</head>
<body>
<main class="canvas">
  <article class="business-card">
    <header class="brand-band">
      <div class="brand-mark"></div>
      <div class="brand-name">Clear Path Coaching</div>
    </header>
    <section class="contact-area">
      <div class="person">
        <p class="person-name">Rebecca Tanfield</p>
        <p class="person-role">Director</p>
        <p class="person-company">Clear Path Coaching</p>
      </div>
      <div class="divider"></div>
      <ul class="contact-list">
        <li class="contact-item">
          <svg class="contact-icon" viewBox="0 0 24 24" aria-hidden="true">
            <path d="M6.6 2.5l3 3.4-1.8 2.6c1.2 2.6 3.2 4.6 5.7 5.8l2.6-1.8 3.4 3-1.6 3.3c-.4.7-1.2 1.1-2 .9C9 18.3 5.7 15 4.3 8.1c-.2-.8.2-1.6.9-2z" fill="#1b1b1b"/>
          </svg>
          <span>0491 362 517</span>
        </li>
        <li class="contact-item">
          <svg class="contact-icon" viewBox="0 0 24 24" aria-hidden="true">
            <rect x="2" y="5" width="20" height="14" fill="#1b1b1b"/>
            <path d="M2.5 5.5L12 13l9.5-7.5" fill="none" stroke="#2ccfd3" stroke-width="1.6"/>
          </svg>
          <span>bec@clearpathcoaching.example.au</span>
        </li>
        <li class="contact-item">
          <svg class="contact-icon" viewBox="0 0 24 24" aria-hidden="true">
            <circle cx="12" cy="12" r="10" fill="#1b1b1b"/>
            <g fill="none" stroke="#2ccfd3" stroke-width="1.3">
              <ellipse cx="12" cy="12" rx="4.2" ry="10"/>
              <line x1="2" y1="12" x2="22" y2="12"/>
              <line x1="4" y1="7" x2="20" y2="7"/>
              <line x1="4" y1="17" x2="20" y2="17"/>
            </g>
          </svg>
          <span>www.clearpathcoaching.example.au</span>
        </li>
      </ul>
    </section>
  </article>
</main>
</body>
</html>
```